Business Cards for IT Consulting Company (Managed Service Provider)

I am looking to have some business cards printed and would like some designs. We are an IT Consulting company based in Vancouver BC. I would like a nice clean and modern look to the cards. I have uploaded all the versions of my logo so parts can be used as needed. Here is a snippit from our website homepage:

Quillbrook Networks Ltd. is an IT Solutions Partner located in Vancouver BC, Canada. We offer IT solutions and support to customers in the greater Vancouver Area. With expertise in Microsoft platforms, as well as Linux and Mac OSX and over 12 years experience in the IT industry, Quillbrook Networks is dedicated to offering our clients top quality service and products. We take pride in the solutions we offer our customers. The greatest compliment a client can give us is to recommend our services.

Quillbrook Networks Ltd. offers a wide range of IT services from onsite service to remote support and managed service solutions. This allows clients to choose the support path that best suits their company’s needs. Supporting many different sized companies from small to enterprise level over the past 12 years Quillbrook Networks has the experience and expertise needed to ensure things run smoothly. Allowing our clients to focus on doing business.

Revolutionizing the way IT services are delivered.

Quillbrook Networks is dedicated to providing our clients with IT solutions that work and grow with them for years to come. This philosophy helps save money in the long run instead of replacing equipment constantly. Far too often IT solutions are not well thought out and while possibly solving the problem at hand, require replacement due to growth or quality within a very short time frame. Quillbrook Networks takes pride in providing solutions that will last and be able to accommodate growth without the need for replacement.

Industry/Entity Type

Information Technology

Contact Information for Business Card

Quillbrook Networks Ltd.
(Employee Name)
Eml: (Employees Email Address)
Web: quillbrook.me
Ph: 604-555-0148

Font styles to use
Serif
Sans Serif

Requirements
Must have
• The Company logo and company colors.
Nice to have
• - Our tag line: "Building Lasting IT Solutions" or "Revolutionizing the way IT services are delivered."
• - Also I really like the idea of nature and technology together blending which is sort of where my logo came from so integrating that somehow onto the business cards would be great.

```html
<!DOCTYPE html>
<html lang="en">
<head>
<meta charset="utf-8">
<title>Quillbrook Networks Ltd. – Business Cards</title>
<link href="https://fonts.googleapis.com/css2?family=Roboto:ital,wght@0,400;0,500;0,700;1,400&display=swap" rel="stylesheet">
<style>
  :root {
    --stage: #a9a7a7;
    --card-dark: #1d1d1f;
    --card-light: #f1f1f1;
    --brand-blue: #1a8bd3;
    --brand-grey: #4a4a4c;
    --ink: #3c3c3e;
    --ink-soft: #555558;
    --tag-light: #e6e6e6;
    --white: #ffffff;
  }
  * { box-sizing: border-box; margin: 0; padding: 0; }
  html, body {
    width: 1200px; height: 1200px; overflow: hidden;
    background: var(--stage);
    font-family: "Roboto", Arial, sans-serif;
  }
  .canvas { position: relative; width: 1200px; height: 1200px; }

  .card { position: absolute; width: 712px; height: 418px; overflow: hidden; }

  /* Company name block: one colour, one weight, one size */
  .brand { position: absolute; display: flex; align-items: center; }
  .brand__mark { background: var(--brand-blue); flex: none; }
  .brand__name {
    color: var(--brand-blue); font-weight: 500; line-height: 1.05;
  }

  /* Front */
  .card--front { left: 238px; top: 118px; background: var(--card-dark); }
  .card--front .brand { left: 112px; top: 134px; gap: 22px; }
  .card--front .brand__mark { width: 22px; height: 22px; }
  .card--front .brand__name { font-size: 54px; }

  .tagline-front {
    position: absolute; left: 0; right: 0; bottom: 20px;
    display: flex; justify-content: center; align-items: center; gap: 16px;
    color: var(--tag-light); font-size: 19px;
  }
  .tagline-front .rule { width: 108px; height: 3px; background: var(--brand-blue); }

  /* Back */
  .card--back { left: 230px; top: 644px; background: var(--card-light); }
  .person { position: absolute; left: 41px; top: 66px; }
  .person__name { color: var(--brand-blue); font-size: 26px; font-weight: 700; }
  .person__role { color: var(--ink-soft); font-size: 16px; font-style: italic; margin-top: 6px; }

  .contacts { position: absolute; left: 40px; top: 244px; list-style: none; }
  .contacts li {
    display: flex; align-items: center; gap: 18px;
    color: var(--ink); font-size: 18px; height: 27.5px;
  }
  .contacts svg { width: 18px; height: 18px; fill: var(--brand-blue); flex: none; }

  .card--back .brand { left: 400px; top: 160px; gap: 14px; }
  .card--back .brand__mark { width: 16px; height: 16px; }
  .card--back .brand__name { font-size: 38px; }

  .wave { position: absolute; left: 0; bottom: 0; width: 712px; height: 418px; }
  .tagline-back {
    position: absolute; right: 52px; bottom: 22px;
    color: var(--white); font-size: 19px;
  }
</style>
</head>
<body>
<main class="canvas">

  <section class="card card--front" aria-label="Card front">
    <div class="brand">
      <div class="brand__mark"></div>
      <p class="brand__name">Quillbrook<br>Networks Ltd.</p>
    </div>
    <p class="tagline-front"><span class="rule"></span>Building Lasting IT Solutions<span class="rule"></span></p>
  </section>

  <section class="card card--back" aria-label="Card back">
    <svg class="wave" viewBox="0 0 712 418" aria-hidden="true">
      <path d="M110 418 Q380 340 712 335 L712 418 Z" fill="#4a4a4c"/>
      <path d="M128 418 Q400 352 712 347 L712 418 Z" fill="#1a8bd3"/>
    </svg>

    <div class="person">
      <h1 class="person__name">Daniel Marsh</h1>
      <p class="person__role">Managing Director</p>
    </div>

    <ul class="contacts">
      <li>
        <svg viewBox="0 0 24 24"><path d="M6.6 10.8a15.1 15.1 0 0 0 6.6 6.6l2.2-2.2a1 1 0 0 1 1-.25 11.4 11.4 0 0 0 3.6.57 1 1 0 0 1 1 1V20a1 1 0 0 1-1 1A17 17 0 0 1 3 4a1 1 0 0 1 1-1h3.5a1 1 0 0 1 1 1c0 1.25.2 2.45.57 3.6a1 1 0 0 1-.25 1z"/></svg>
        604-555-0148
      </li>
      <li>
        <svg viewBox="0 0 24 24"><path d="M12 2a10 10 0 1 0 0 20 10 10 0 0 0 0-20zm6.9 6h-2.9a15.7 15.7 0 0 0-1.4-3.6A8 8 0 0 1 18.9 8zM12 4c.8 1.2 1.5 2.5 1.9 4h-3.8c.4-1.5 1.1-2.8 1.9-4zM4.3 14a8 8 0 0 1 0-4h3.4a16 16 0 0 0 0 4zm.8 2h2.9c.3 1.3.8 2.5 1.4 3.6A8 8 0 0 1 5.1 16zM8 8H5.1a8 8 0 0 1 4.3-3.6C8.8 5.5 8.3 6.7 8 8zm4 12c-.8-1.2-1.5-2.5-1.9-4h3.8c-.4 1.5-1.1 2.8-1.9 4zm2.3-6H9.7a14.6 14.6 0 0 1 0-4h4.6a14.6 14.6 0 0 1 0 4zm.3 5.6c.6-1.1 1.1-2.3 1.4-3.6h2.9a8 8 0 0 1-4.3 3.6zM16.3 14a16 16 0 0 0 0-4h3.4a8 8 0 0 1 0 4z"/></svg>
        www.quillbrook.me
      </li>
      <li>
        <svg viewBox="0 0 24 24"><path d="M2 5h20v14H2zm2 2v.4l8 5 8-5V7zm0 2.8V17h16V9.8l-8 5z"/></svg>
        support@quillbrook.me
      </li>
    </ul>

    <div class="brand">
      <div class="brand__mark"></div>
      <p class="brand__name">Quillbrook<br>Networks Ltd.</p>
    </div>

    <p class="tagline-back">Building Lasting IT Solutions</p>
  </section>

</main>
</body>
</html>
```